Home Security Company Business Card

Looking for a eye catching business card that is non traditional and stands out but yet still looks professional. It should include all the pertinent information such as name, title, address, telephone, e-mail, website address should definitely stand out and then finally the logo.

Target Market(s)

Residential and Commercial accounts mostly upscale accounts

Industry/Entity Type

Security

Contact Information for Business Card

Name
Title
Address
Office #
Cell #
E-mail
Website

Font styles to use
Serif
Sans Serif

Requirements
Must have
• Logo, two sided color configuration
Nice to have
• You decide
Should not have
• There really aren't any.

```html
<!DOCTYPE html>
<html lang="en">
<head>
<meta charset="utf-8">
<title>Ironvale Security Systems – Business Card</title>
<link href="https://fonts.googleapis.com/css2?family=Open+Sans:wght@400;600&display=swap" rel="stylesheet">
<style>
  :root {
    --backdrop: #3b3431;
    --card: #1c1c1d;
    --card-edge: #111112;
    --gold: #e9a323;
    --gold-deep: #c9861a;
    --brand-red: #9a2414;
    --ink-light: #f2f2f2;
    --divider: #3a3a3c;
  }
  * { box-sizing: border-box; margin: 0; padding: 0; }
  html, body {
    width: 1200px; height: 844px; overflow: hidden;
    background: var(--backdrop);
    font-family: "Open Sans", Arial, sans-serif;
  }
  .stage {
    position: relative; width: 1200px; height: 844px;
    display: flex; align-items: center; justify-content: center; gap: 60px;
  }
  .card {
    position: relative; width: 520px; height: 297px;
    background: radial-gradient(ellipse at 40% 30%, #242425 0%, var(--card) 60%, var(--card-edge) 100%);
    box-shadow: 0 14px 30px rgba(0,0,0,.45);
  }
  /* brand lockup */
  .brand { display: flex; align-items: center; gap: 10px; color: var(--ink-light); font-weight: 600; }
  .brand-mark { width: 34px; height: 34px; border-radius: 50%; background: var(--gold); flex: none; }
  .brand-text { line-height: 1; }
  .brand-name { display: block; font-size: 20px; letter-spacing: 1px; }
  .brand-sub { display: block; font-size: 7.5px; letter-spacing: .6px; margin-top: 3px; }

  /* front side */
  .card-front .brand { position: absolute; left: 178px; top: 58px; }
  .person {
    position: absolute; right: 275px; top: 150px; text-align: right;
    color: var(--ink-light);
  }
  .person-name { color: var(--gold); font-weight: 600; font-size: 16px; }
  .person-title { font-size: 12px; margin-top: 1px; }
  .person-address { font-size: 13px; line-height: 1.35; margin-top: 12px; }
  .divider {
    position: absolute; left: 262px; top: 148px; width: 1px; height: 100px;
    background: var(--divider);
  }
  .contacts {
    position: absolute; left: 278px; top: 146px; list-style: none;
    color: var(--ink-light); font-size: 12.5px; line-height: 19px;
  }
  .contacts li { display: flex; align-items: center; gap: 8px; }
  .contacts svg { width: 10px; height: 10px; fill: var(--gold); flex: none; }

  /* back side */
  .card-back .brand {
    position: absolute; left: 50%; top: 50%; transform: translate(-50%, -50%);
    color: var(--brand-red); gap: 14px;
  }
  .card-back .brand-mark { width: 62px; height: 62px; }
  .card-back .brand-name { font-size: 30px; }
  .card-back .brand-sub { font-size: 10px; margin-top: 4px; }
</style>
</head>
<body>
<main class="stage">

  <section class="card card-front" aria-label="Business card front">
    <div class="brand">
      <span class="brand-mark"></span>
      <span class="brand-text">
        <span class="brand-name">IRONVALE</span>
        <span class="brand-sub">SECURITY SYSTEMS INC.</span>
      </span>
    </div>

    <div class="person">
      <p class="person-name">Daniel Harper</p>
      <p class="person-title">Managing Director</p>
      <p class="person-address">12345, Address Goes Here<br>Country Name, 123456.</p>
    </div>

    <span class="divider"></span>

    <ul class="contacts">
      <li>
        <svg viewBox="0 0 10 10" aria-hidden="true"><path d="M1 3.2C1 2 2 1.5 3 1.5h4c1 0 2 .5 2 1.7V4H7V3H3v1H1zM2 5h6l1 3.5H1z"/></svg>
        044-555 210 480
      </li>
      <li>
        <svg viewBox="0 0 10 10" aria-hidden="true"><path d="M3 0h4a1 1 0 0 1 1 1v8a1 1 0 0 1-1 1H3a1 1 0 0 1-1-1V1a1 1 0 0 1 1-1zm0 1.5v6h4v-6z"/></svg>
        044-555 210 480
      </li>
      <li>
        <svg viewBox="0 0 10 10" aria-hidden="true"><path d="M0 2h10v6H0zM.8 2.6 5 5.6l4.2-3H.8z"/></svg>
        info@ironvalesecure.com
      </li>
      <li>
        <svg viewBox="0 0 10 10" aria-hidden="true"><path d="M6.5 1 9 3.5 7.2 5.3 6.4 4.5 7.6 3.5 6.5 2.4 5.3 3.6 4.5 2.8zM3.5 9 1 6.5 2.8 4.7l.8.8-1.2 1 1.1 1.1 1.2-1.2.8.8zM3.2 6.1 6.1 3.2l.7.7-2.9 2.9z"/></svg>
        www.ironvalesecure.com
      </li>
    </ul>
  </section>

  <section class="card card-back" aria-label="Business card back">
    <div class="brand">
      <span class="brand-mark"></span>
      <span class="brand-text">
        <span class="brand-name">IRONVALE</span>
        <span class="brand-sub">SECURITY SYSTEMS INC.</span>
      </span>
    </div>
  </section>

</main>
</body>
</html>
```